Homemaking training schools needs a Business Card design

Designer, Hello!

No special requirements, good-looking enough.
--------------------------------------------------------------------------

Name: Marcus Dole
Chairman
Tel: 0574-71948263
Mobile: 13857420916
Email: kelvora@mailnest.example
Web: www.prt2019.example
Add: No.258, LanpingJie, BeiyuanQu, Ningbo, Zhejiang

LOGO
Ningbo PRT Homemaking Training School

Target Market(s)

pregnant women, mothers, infants, the elderly and families, including cleaning, cooking, nursing training.

Industry/Entity Type

Business

Contact Information for Business Card

Name: Marcus Dole
Chairman
Tel: 0574-71948263
Mobile: 13857420916
Email: kelvora@mailnest.example
Web: www.prt2019.example

LOGO

Font styles to use
Serif
Sans Serif
Decorative

Requirements
Nice to have
• Feels: clean, specifications, safety, comfort, warmth and happiness.

```html
<!DOCTYPE html>
<html lang="en">
<head>
<meta charset="UTF-8">
<title>PingRuiTang Business Card</title>
<link rel="stylesheet" href="https://fonts.googleapis.com/css2?family=Montserrat:wght@400;500;600;700;800&display=swap">
<style>
  :root {
    --stage: #2b2b2d;
    --card-black: #000000;
    --brand-blue: #1274bd;
    --brand-pink: #e6058f;
    --ink-white: #ffffff;
    --card-w: 640px;
    --card-h: 366px;
    --radius: 22px;
  }
  * { box-sizing: border-box; margin: 0; padding: 0; }
  html, body {
    width: 1200px; height: 900px; overflow: hidden;
    background: var(--stage);
    font-family: "Montserrat", Arial, sans-serif;
  }
  .stage { position: relative; width: 1200px; height: 900px; }
  .card {
    position: absolute;
    width: var(--card-w); height: var(--card-h);
    border-radius: var(--radius);
    background: var(--card-black);
    overflow: hidden;
    box-shadow: 0 14px 30px rgba(0,0,0,0.45);
  }
  .card--back { left: 280px; top: 46px; }
  .card--front { left: 280px; top: 488px; }

  /* Back side */
  .back-mark {
    position: absolute; left: 0; right: 0; top: 112px;
    display: flex; flex-direction: column; align-items: center; gap: 14px;
  }
  .back-mark__dot {
    width: 46px; height: 46px; border-radius: 50%;
    background: var(--brand-pink);
  }
  .back-mark__name {
    color: var(--ink-white); font-weight: 600; font-size: 38px; letter-spacing: 0.5px;
  }
  .back-web {
    position: absolute; left: 0; right: 0; top: 288px;
    text-align: center; color: var(--ink-white);
    font-weight: 700; font-size: 17px; letter-spacing: 0.5px;
  }
  .back-web .accent { color: var(--brand-pink); }

  /* Front side */
  .front-shape { position: absolute; inset: 0; }
  .brand {
    position: absolute; left: 30px; top: 128px; width: 330px;
    display: flex; flex-direction: column; align-items: center;
  }
  .brand__row { display: flex; align-items: center; gap: 10px; }
  .brand__dot {
    width: 16px; height: 16px; border-radius: 50%; background: var(--brand-pink);
  }
  .brand__name {
    color: var(--ink-white); font-weight: 700; font-size: 38px; letter-spacing: 0.3px;
  }
  .brand__tagline {
    margin-top: 6px; display: flex; align-items: center; gap: 10px;
    color: var(--ink-white); font-weight: 400; font-size: 15px; letter-spacing: 0.5px;
  }
  .brand__rule { width: 60px; height: 1px; background: var(--ink-white); }

  .contact {
    position: absolute; left: 400px; top: 72px; width: 230px;
    color: var(--ink-white);
  }
  .contact__name {
    color: var(--brand-pink); font-weight: 800; font-size: 27px; letter-spacing: 0.5px;
    line-height: 1;
  }
  .contact__role {
    margin-top: 6px; font-weight: 600; font-size: 12px; letter-spacing: 1px;
  }
  .contact__address {
    margin-top: 12px; font-weight: 500; font-size: 12.5px; line-height: 1.45;
  }
  .contact__list { margin-top: 12px; list-style: none; }
  .contact__item {
    display: flex; align-items: center; gap: 8px;
    font-weight: 600; font-size: 12.5px; line-height: 1.55;
  }
  .contact__icon { width: 11px; height: 11px; flex: none; }
</style>
</head>
<body>
<main class="stage">

  <section class="card card--back" aria-label="Card back">
    <div class="back-mark">
      <span class="back-mark__dot"></span>
      <span class="back-mark__name">PingRuiTang</span>
    </div>
    <p class="back-web">www.<span class="accent">prt2019</span>.example</p>
  </section>

  <section class="card card--front" aria-label="Card front">
    <svg class="front-shape" width="640" height="366" viewBox="0 0 640 366" aria-hidden="true">
      <path d="M0 0 L250 0 C 385 40 420 250 355 366 L0 366 Z" fill="var(--brand-blue)"/>
      <path d="M262 -4 C 398 40 436 250 372 370" fill="none" stroke="var(--brand-pink)" stroke-width="3"/>
    </svg>

    <div class="brand">
      <div class="brand__row">
        <span class="brand__dot"></span>
        <span class="brand__name">PingRuiTang</span>
      </div>
      <div class="brand__tagline">
        <span class="brand__rule"></span>
        <span>Training &amp; Services</span>
        <span class="brand__rule"></span>
      </div>
    </div>

    <div class="contact">
      <h1 class="contact__name">MARCUS DOLE</h1>
      <p class="contact__role">CHAIRMAN</p>
      <p class="contact__address">258, LanpingJie<br>BeiyuanQu, Ningbo, Zhejiang</p>
      <ul class="contact__list">
        <li class="contact__item">
          <svg class="contact__icon" viewBox="0 0 12 12"><path d="M2 1 L4.5 1 L5.5 3.5 L4 4.5 C4.8 6.2 5.8 7.2 7.5 8 L8.5 6.5 L11 7.5 L11 10 C11 10.6 10.6 11 10 11 C5 11 1 7 1 2 C1 1.4 1.4 1 2 1 Z" fill="var(--brand-pink)"/></svg>
          <span>0574-71948263</span>
        </li>
        <li class="contact__item">
          <svg class="contact__icon" viewBox="0 0 12 12"><rect x="3" y="0.5" width="6" height="11" rx="1.2" fill="none" stroke="var(--brand-pink)" stroke-width="1.3"/><circle cx="6" cy="9.4" r="0.7" fill="var(--brand-pink)"/></svg>
          <span>13857420916</span>
        </li>
        <li class="contact__item">
          <svg class="contact__icon" viewBox="0 0 12 12"><rect x="0.7" y="2" width="10.6" height="8" rx="1" fill="none" stroke="var(--brand-pink)" stroke-width="1.3"/><path d="M1 2.5 L6 6.5 L11 2.5" fill="none" stroke="var(--brand-pink)" stroke-width="1.2"/></svg>
          <span>kelvora@mailnest.example</span>
        </li>
        <li class="contact__item">
          <svg class="contact__icon" viewBox="0 0 12 12"><circle cx="6" cy="6" r="5" fill="none" stroke="var(--brand-pink)" stroke-width="1.2"/><ellipse cx="6" cy="6" rx="2.2" ry="5" fill="none" stroke="var(--brand-pink)" stroke-width="1"/><path d="M1 6 H11" stroke="var(--brand-pink)" stroke-width="1"/></svg>
          <span>www.prt2019.example</span>
        </li>
      </ul>
    </div>
  </section>

</main>
</body>
</html>
```